San Francisco Leading Consulting firm - 47Vora Web Design Project

•Create a Web Design
•Uncoded webpage layout design
•2 Pages Design - Homepage + Interior Page

Task Description
Hello, we're looking for a re-design our current website www.47vora-example.com

we have a sample mockup design @

http://47vora.pubtrellis-example.org/

This shows the layout that we like and also a sample of 6 pictures that would change based on where you mouse over..

6 pictures HOME design needs to be included.

SMART
THOUGHTFUL
FLEXIBLE
CREATIVE SERVICES
TECHNICAL SERVICES
PARTNERS

sites we like:

http://www.melvanadvisory-example.com/Home.cfm?id=Home
http://www.plinthworks-example.com/index.html

Our company can be best described as: 100+ employees, cutting-edge, depandable, innovative, strong, smart.

Our Primary focus is: IT Consulting Services and Creative Design services

47Vora LLC is a consulting firm providing creative design, business and technology solutions to both private and public interests.

Established in 1996, 47Vora is a San Francisco based company providing specialists for a range of business needs including:

Creative Design Services
•Print
•Logo Design
•Website Design
•Illustration

and

Business and Technology solutions

•Application Software and Web Development
•Business Process Re-Design (BPR)
•Business/Systems Analysis and Requirement Documentation
•Mentoring and Training
•Network/Hardware Installation Services
•System Design and Architecture
•Vendor Management
•Docuvault Architecture and Implementation

our sample mockup site:

Reason: Due to holiday season, we're not available to work with designers and finilize our design.  

Thank you very much for submitting your design.

We appreciate your time and creativity.   Since, our office is currently closed for holidays, we will be reviewing it in details next week and will make our decision as soon as possible.

It would be great if you could submit any of your changes by Wed next week, so it would be part of our reviews. 

Please see updated wireframe under attachments:  we have some minor updates to our wireframe that we would like you to update your designs, if possible.  

We also encorouge you not to use our standard wireframe and come up with more unique designs.   Everything would be considered when we review your design.

 

Target Market(s)

Creative services and professional services clients, including government agencies

Industry/Entity Type

Business

Requirements
Must have
• Clean, professional look, easy navigation

```html
<!DOCTYPE html>
<html lang="en">
<head>
<meta charset="utf-8">
<title>47Vora – Consulting</title>
<link href="https://fonts.googleapis.com/css2?family=Arimo:wght@400;700&family=Open+Sans:wght@400;600&family=Raleway:wght@300&display=swap" rel="stylesheet">
<style>
:root{
  --ink:#111;
  --dark:#1b1c1d;
  --panel:#0f1011;
  --text:#333;
  --blue:#1d2fd8;
  --link:#1a3fd0;
  --tile-top:#37b4f0;
  --tile-bot:#1e7fe0;
  --white:#fff;
  --footer-text:#c9c9c9;
}
*{margin:0;padding:0;box-sizing:border-box}
html,body{width:1118px;height:1200px;overflow:hidden;background:var(--white)}
body{font-family:Arimo,Arial,sans-serif;color:var(--text)}
.stage{position:relative;width:1200px;height:1288px;transform:scale(0.93167);transform-origin:0 0}
.abs{position:absolute}

/* header */
.header{left:97px;top:0;width:1007px;height:135px;background:linear-gradient(180deg,#f2f2f2,#cfcfcf 70%,#d9d9d9);overflow:hidden}
.header svg{position:absolute;left:0;top:0}
.brand{left:88px;top:48px;display:flex;align-items:center;gap:14px;font-family:Raleway,sans-serif;font-weight:300;font-size:46px;color:#2a2a2a;letter-spacing:2px}
.brand i{display:block;width:26px;height:26px;border-radius:50%;background:#2a8fe0}
.nav{left:471px;top:95px;width:633px;height:40px;background:var(--ink);display:flex;align-items:center;padding-left:26px;font-size:14px;color:var(--white)}
.nav span.sep{margin:0 20px}

/* hero */
.hero{left:97px;top:135px;width:1007px;height:388px;background:var(--dark)}
.hero-photo{left:13px;top:12px;width:697px;height:363px;background:radial-gradient(ellipse at 70% 40%,#e4e4e4,#8a8a8a 45%,#2c2c2c 90%)}
.hero-caption{left:27px;top:132px;font-family:"Open Sans",sans-serif;font-size:26px;color:var(--white)}
.hero-panel{left:710px;top:12px;width:283px;height:293px;background:var(--panel)}
.hero-frame{left:726px;top:47px;width:260px;height:250px;border:1px solid #3a3a3a}
.hero-title{left:737px;top:32px;width:236px;height:33px;background:#262728;color:var(--white);font-size:20px;padding:6px 0 0 9px}
.hero-text{left:741px;top:80px;width:234px;font-size:11.5px;line-height:20px;color:#e0e0e0;text-align:justify}
.readmore{left:900px;top:267px;width:80px;height:25px;background:#3b3c3d;color:#eee;font-size:13px;text-align:center;line-height:25px}
.slider{left:721px;top:317px;width:275px;height:56px;background:linear-gradient(90deg,#2a2c2e,#1c1e20 50%,#3a3c3e)}
.slider svg{position:absolute;top:0;left:0}

/* content */
.content{left:97px;top:523px;width:1007px;height:524px;background:linear-gradient(180deg,#edf0f2,#fbfbfc)}
.h2{font-size:16px;color:var(--ink)}
.h2 b{font-weight:400;color:var(--blue)}
.rule{height:1px;background:#dcdcdc}
.client-box{left:122px;top:593px;width:284px;height:172px;background:var(--white);border:1px solid #dadada;display:flex;align-items:center;justify-content:center;gap:10px;font-size:34px;color:#343c7c}
.client-box i{display:block;width:22px;height:22px;background:#f07a1a}
.para{font-size:11.5px;line-height:18px;color:var(--text);text-align:justify}
.btn-black{background:var(--ink);color:var(--white);font-size:12px;border-radius:4px;text-align:center;line-height:22px;height:22px}
.services{left:456px;top:591px;width:290px;list-style:none;font-size:12px;color:#222}
.services li{position:relative;padding:0 0 0 10px;margin-bottom:8px;line-height:20px}
.services li::before{content:"";position:absolute;left:1px;top:7px;border-left:4px solid #444;border-top:3px solid transparent;border-bottom:3px solid transparent}
.services li span{display:inline-block;border-bottom:1px dotted #888;padding-bottom:2px}
.services li.active{color:var(--link)}
.partner-photo{left:782px;top:595px;width:106px;height:106px;border:2px solid #7fe0ef;background:linear-gradient(135deg,#cfe6ee,#c98a6a 45%,#8c4a36 70%,#d9ecf0)}

/* graphic tiles */
.tiles{left:120px;top:936px;width:952px;height:154px;border:1px solid #0b2a4a;border-radius:5px;background:linear-gradient(180deg,var(--tile-bot),var(--tile-top) 45%,var(--tile-bot));display:flex;overflow:hidden}
.tile{position:relative;border-right:1px solid #ffffff;height:100%}
.tile:last-child{border-right:none}
.tile h3{font-weight:400;font-size:18px;color:var(--white);text-align:center;margin-top:8px}
.tile .line{position:absolute;top:40px;height:1px;background:#fff}
.tile .art{position:absolute;top:54px;width:80px;height:74px;border-radius:6px}
.more{position:absolute;bottom:4px;height:18px;background:var(--white);border-radius:2px;font-size:11px;color:#1d4fb0;display:flex;align-items:center}
.more span{padding:0 6px}
.more em{font-style:normal;border-left:1px solid #bbb;padding:0 6px;font-weight:700}

/* footer */
.footer{left:97px;top:1047px;width:1007px;height:241px;background:#0a0a0a}
.fcol{top:1114px;font-size:12px;color:var(--footer-text)}
.fcol h4{font-weight:400;color:var(--white);font-size:12px;padding-bottom:9px;border-bottom:1px dotted #444;width:150px;margin-bottom:14px}
.fcol ul{list-style:none;font-size:11px}
.fcol li{margin-bottom:10px}
.fcol li.arr::before{content:"»";margin-right:7px;color:#888}
.fcol li.soc{display:flex;align-items:center;gap:6px;margin-bottom:6px}
.fcol li.soc i{display:block;width:14px;height:12px;background:#3b78c8}
.fdivider{left:926px;top:1120px;width:1px;height:145px;background:#2a2a2a}
.flogo{left:942px;top:1180px;display:flex;align-items:center;gap:8px;font-family:Raleway,sans-serif;font-weight:300;font-size:24px;color:#bcbcbc;letter-spacing:1px}
.flogo i{display:block;width:14px;height:14px;border-radius:50%;background:#2a9ae8}
</style>
</head>
<body>
<div class="stage">

  <header class="header abs">
    <svg width="1007" height="135" aria-hidden="true">
      <path d="M0 118 C200 60 500 40 1007 50" fill="none" stroke="#ffffff" stroke-width="14" opacity=".55"/>
      <path d="M860 135 C900 60 960 20 1007 5" fill="none" stroke="#ffffff" stroke-width="2" opacity=".7"/>
    </svg>
    <div class="brand abs"><i></i>47VORA</div>
  </header>
  <nav class="nav abs">
    <span>Copmany</span><span class="sep">|</span>
    <span>Technical Services</span><span class="sep">|</span>
    <span>Creative Services</span><span class="sep">|</span>
    <span>Partners</span><span class="sep">|</span>
    <span>Contact Us</span>
  </nav>

  <section class="hero abs">
    <div class="hero-photo abs" role="img" aria-label="Black and white photo of a hand on a laptop touchpad"></div>
    <div class="hero-caption abs">Technical services</div>
    <div class="hero-panel abs"></div>
    <div class="hero-frame abs"></div>
    <div class="hero-title abs">TECHNICAL SERVICES</div>
    <p class="hero-text abs">Lorem Ipsum is simply dummy text of the printing and typesetting industry. Lorem Ipsum has been the industry's standard dummy text ever since the 1500s, when an unknown printer took a galley of type and scrambled it to make a type specimen book.</p>
    <div class="readmore abs">readmore</div>
    <div class="slider abs">
      <svg width="275" height="56" aria-hidden="true">
        <rect x="4" y="6" width="40" height="40" fill="#111"/>
        <path d="M31 14 L19 26 L31 38" fill="none" stroke="#fff" stroke-width="4"/>
        <path d="M246 14 L258 26 L246 38" fill="none" stroke="#fff" stroke-width="4"/>
      </svg>
    </div>
  </section>

  <section class="content abs"></section>

  <!-- clients -->
  <div class="h2 abs" style="left:137px;top:551px">Our <b>Clients</b></div>
  <div class="rule abs" style="left:123px;top:582px;width:282px"></div>
  <div class="client-box abs"><i></i>Nirvik</div>
  <p class="para abs" style="left:125px;top:773px;width:277px">Lorem Ipsum is simply dummy text of the printing and typesetting industry. Lorem Ipsum has been the industry's standard dummy text ever since the 1500s, when an unknown printer took a galley of type and scrambled it to specimen book.</p>
  <div class="btn-black abs" style="left:127px;top:872px;width:69px">View all</div>

  <!-- services -->
  <div class="h2 abs" style="left:460px;top:555px">Our <b>Services</b></div>
  <div class="rule abs" style="left:458px;top:582px;width:282px"></div>
  <ul class="services abs">
    <li class="active"><span>Business and Technology solutions</span></li>
    <li><span>Application Software and Web Development</span></li>
    <li><span>Business Process Re-Design (BPR)</span></li>
    <li><span>Business/Systems Analysis and Requirement Documentation</span></li>
    <li><span>Mentoring and Training</span></li>
    <li><span>Business and Technology solutions</span></li>
    <li><span>Business and Technology solutions</span></li>
    <li><span>Vendor Management</span></li>
    <li><span>Docuvault Architecture and Implementation</span></li>
  </ul>

  <!-- partners -->
  <div class="h2 abs" style="left:782px;top:555px">For <b>partners</b></div>
  <div class="rule abs" style="left:780px;top:582px;width:292px"></div>
  <div class="partner-photo abs" role="img" aria-label="Photo of four hands gripping wrists in a square, teamwork"></div>
  <p class="para abs" style="left:895px;top:591px;width:176px;line-height:20px">Lorem Ipsum is simply dummy text of the printing and typesetting industry. Lorem Ipsum has been the industry's standard dummy text ever since the 1500s, when an unknown</p>
  <p class="para abs" style="left:784px;top:708px;width:288px;line-height:20px">Lorem Ipsum is simply dummy text of the printing and typesetting industry. Lorem Ipsum has been the industry's standard dummy text ever since the 1500s, when an unknown printer took a galley of type and scrambled it to make a type specimen book. It has survived not only five centuries, but alsounchanged. It was popularised in the 1960sns of Lorem Ipsum.</p>
  <div class="btn-black abs" style="left:1002px;top:872px;width:69px">Read More</div>

  <!-- graphic designers -->
  <footer class="footer abs"></footer>
  <div class="h2 abs" style="left:123px;top:910px">For <b>graphic designers</b></div>
  <div class="tiles abs">
    <div class="tile" style="width:232px">
      <h3>Print</h3><div class="line" style="left:7px;width:211px"></div>
      <div class="art" style="left:65px;background:linear-gradient(135deg,#d8dde3,#c0392b 60%,#7a2a2a)" role="img" aria-label="Illustration of a billboard being painted"></div>
      <div class="more" style="left:160px"><span>More</span><em>»</em></div>
    </div>
    <div class="tile" style="width:228px">
      <h3>Logo Design</h3><div class="line" style="left:13px;width:199px"></div>
      <div class="art" style="left:64px;background:radial-gradient(circle,#f07a2a,#c8321e 60%,transparent 72%)" role="img" aria-label="Illustration of a round emblem"></div>
      <div class="more" style="left:158px"><span>More</span><em>»</em></div>
    </div>
    <div class="tile" style="width:246px">
      <h3>Web Design</h3><div class="line" style="left:14px;width:211px"></div>
      <div class="art" style="left:82px;width:60px;background:linear-gradient(180deg,#e8c06a,#8fb6d8 60%,#cfe4f2)" role="img" aria-label="Illustration of brushes in a glass jar"></div>
      <div class="more" style="left:169px"><span>More</span><em>»</em></div>
    </div>
    <div class="tile" style="width:246px">
      <h3>Illustration</h3><div class="line" style="left:19px;width:211px"></div>
      <div class="art" style="left:80px;background:linear-gradient(135deg,#b9e08a,#6f9e3a 50%,#3c3a2a)" role="img" aria-label="Illustration of a takeaway box with chopsticks"></div>
      <div class="more" style="left:174px"><span>More</span><em>»</em></div>
    </div>
  </div>

  <div class="fcol abs" style="left:133px">
    <h4>Quick Linka</h4>
    <ul>
      <li class="arr">Copmany</li><li class="arr">Technical Services</li><li class="arr">Creative Services</li><li class="arr">Partners</li><li class="arr">Contact Us</li>
    </ul>
  </div>
  <div class="fcol abs" style="left:313px">
    <h4>Contact</h4>
    <ul><li style="margin-bottom:6px">UK: +140227815</li><li style="margin-bottom:6px">USA: +150338926</li><li>text@47vora-example.com</li></ul>
  </div>
  <div class="fcol abs" style="left:494px">
    <h4>Follow Us</h4>
    <ul>
      <li class="soc"><i></i>FRIENDLOOP</li>
      <li class="soc"><i></i>CHIRPLINE</li>
      <li class="soc"><i></i>WORKGRID</li>
    </ul>
  </div>
  <div class="fcol abs" style="left:715px">
    <h4>Graphic Designers</h4>
    <ul><li class="arr">Print</li><li class="arr">Logo Design</li><li class="arr">Website Design</li><li class="arr">Illustration</li></ul>
  </div>
  <div class="fdivider abs"></div>
  <div class="flogo abs"><i></i>47VORA</div>

</div>
</body>
</html>
```